Logo for a Food & Beverage Franchise Company

We need a logo and stationary for a new company that just aquired a restaurant franchise. We need a sleep and professional logo with stationary.

Target Market(s)

Adults, resturaunt owners, franchisors (Companies who own food franchise companies such as Farrowbys Head Office, Toastwell International Franchise)
and Big Food and Beverage who wish to give franchise rights to us)

Industry/Entity Type

Restaurant

Logo Text

Velvet Harbor

Logo styles of interest
Emblem Logo
Pictorial/Combination Logo
Character Logo
Font styles to use
Serif
Sans Serif

Colors
ffc214
f78f20
f37022
faa54b
fece3e
fbed22

Requirements
Must have
• Maximum three color. The less the better.
Nice to have
• It does not have to have a crown, but if you wish to have a crown then it does not have to be so sharp and clear. Abstract is better.

```html
<!DOCTYPE html>
<html lang="en">
<head>
<meta charset="utf-8">
<title>Velvet Harbor — Business Card</title>
<link href="https://fonts.googleapis.com/css2?family=Open+Sans:wght@400;600;700&display=swap" rel="stylesheet">
<style>
  :root {
    --backdrop: #ececec;
    --card: #ffffff;
    --brand-orange: #fca311;
    --ink-dark: #2b2b2b;
    --ink-grey: #6d6d6d;
  }
  * { box-sizing: border-box; margin: 0; padding: 0; }
  html, body {
    width: 1200px;
    height: 800px;
    overflow: hidden;
    background: var(--backdrop);
    font-family: "Open Sans", Arial, sans-serif;
  }
  .stage { position: relative; width: 1200px; height: 800px; }

  .card {
    position: absolute;
    width: 520px;
    height: 300px;
    background: var(--card);
    box-shadow: 0 2px 6px rgba(0,0,0,0.10);
    overflow: hidden;
  }

  /* Front */
  .card--front { left: 170px; top: 80px; }
  .front-band {
    position: absolute;
    left: 180px;
    top: 0;
    width: 170px;
    height: 100%;
    background: var(--brand-orange);
    display: flex;
    align-items: center;
    justify-content: center;
  }
  .front-band__name {
    color: var(--card);
    font-weight: 700;
    font-size: 22px;
    letter-spacing: 3px;
    text-transform: uppercase;
    text-align: center;
    line-height: 1.3;
  }

  /* Back */
  .card--back { left: 510px; top: 420px; }
  .back-band {
    position: absolute;
    left: 50px;
    top: 0;
    width: 90px;
    height: 100%;
    background: var(--brand-orange);
    display: flex;
    align-items: center;
    justify-content: center;
  }
  .back-band__square {
    width: 22px;
    height: 22px;
    background: var(--card);
  }
  .brand-block {
    position: absolute;
    left: 180px;
    right: 30px;
    top: 34px;
    text-align: center;
  }
  .brand-block__square {
    display: block;
    width: 16px;
    height: 16px;
    margin: 0 auto 8px;
    background: var(--brand-orange);
  }
  .brand-block__name {
    color: var(--brand-orange);
    font-weight: 600;
    font-size: 20px;
    letter-spacing: 5px;
    text-transform: uppercase;
  }
  .holder {
    margin-top: 6px;
    color: var(--ink-dark);
    font-weight: 700;
    font-size: 15px;
  }
  .contact-list {
    position: absolute;
    left: 200px;
    top: 170px;
    list-style: none;
    color: var(--ink-grey);
    font-weight: 700;
    font-size: 13px;
    line-height: 1.45;
  }
  .contact-list__address { font-size: 15px; }
</style>
</head>
<body>
<main class="stage">
  <section class="card card--front" aria-label="Business card front">
    <div class="front-band">
      <span class="front-band__name">Velvet<br>Harbor</span>
    </div>
  </section>

  <section class="card card--back" aria-label="Business card back">
    <div class="back-band"><span class="back-band__square"></span></div>
    <div class="brand-block">
      <span class="brand-block__square"></span>
      <div class="brand-block__name">Velvet Harbor</div>
      <div class="holder">Karim Nadeer C.E.O.</div>
    </div>
    <ul class="contact-list">
      <li>Office: +1 555 240 7318</li>
      <li>Mobile: +1 555 610 4427</li>
      <li>Email: karim@velvetharbor.com</li>
      <li class="contact-list__address">P.O. Box 4120, Marlow Bay</li>
    </ul>
  </section>
</main>
</body>
</html>
```